Business Card & Letterhead Design

We a financial advice company based in Australia. We provide advice to wealthy farmers.

We are changing our business name FROM Brightvale Financial TO Tallowmere Wealth and we need a new letterhead and double sided business card design

Attached is designs from our previous branding (Brightvale Financial) as it includes all the details we require on the new Tallowmere Wealth business cards and letterhead.

Need extra days to review

```html
<!DOCTYPE html>
<html lang="en">
<head>
<meta charset="utf-8">
<title>Tallowmere Wealth – Business Card</title>
<link rel="stylesheet" href="https://fonts.googleapis.com/css2?family=Cinzel:wght@400&family=Cormorant+Garamond:wght@500&family=Montserrat:wght@300;400&display=swap">
<style>
  :root {
    --bg: #e9eaeb;
    --slate: #5f6a70;
    --slate-dark: #4d575c;
    --paper: #ffffff;
    --ink: #3f4448;
    --ink-soft: #6d7378;
    --on-slate: #f2f4f5;
  }
  * { box-sizing: border-box; margin: 0; padding: 0; }
  html, body { width: 1200px; height: 900px; overflow: hidden; background: var(--bg); }
  body { position: relative; font-family: "Montserrat", sans-serif; }

  .card {
    position: absolute;
    width: 600px; height: 365px;
    border-radius: 22px;
    overflow: hidden;
    box-shadow: 0 10px 28px rgba(0,0,0,.18);
  }

  /* Front */
  .card--front { left: 110px; top: 70px; background: var(--slate); color: var(--on-slate); }
  .wordmark {
    font-family: "Cinzel", serif;
    font-weight: 400;
    letter-spacing: .02em;
    line-height: 1;
  }
  .tagline {
    font-family: "Montserrat", sans-serif;
    font-weight: 300;
    letter-spacing: .18em;
    font-size: 10px;
    margin-top: 4px;
  }
  .card--front .brand { position: absolute; left: 46px; top: 92px; }
  .card--front .wordmark { font-size: 27px; color: var(--on-slate); }
  .card--front .tagline { color: #cfd5d8; padding-left: 20px; }
  .front-circle {
    position: absolute; right: 48px; top: 40px;
    width: 178px; height: 178px;
    border: 4px solid var(--on-slate); border-radius: 50%;
  }
  .services { list-style: none; position: absolute; left: 46px; top: 160px; }
  .services li {
    font-family: "Cormorant Garamond", serif; font-weight: 500;
    font-size: 19px; letter-spacing: .04em; text-transform: uppercase;
    display: flex; align-items: center; gap: 12px; margin-bottom: 6px;
  }
  .services svg { width: 15px; height: 15px; flex: none; }
  .licensee {
    position: absolute; left: 46px; top: 290px;
    font-size: 14.5px; font-weight: 400; line-height: 1.5; color: var(--on-slate);
  }

  /* Back */
  .card--back { left: 490px; top: 470px; background: var(--paper); color: var(--ink); }
  .card--back .brand { position: absolute; left: 42px; top: 36px; }
  .back-circle {
    width: 52px; height: 52px; border: 2.5px solid var(--ink); border-radius: 50%;
    margin: 0 0 10px 60px;
  }
  .card--back .wordmark { font-size: 25px; color: var(--ink); }
  .card--back .tagline { color: var(--ink-soft); padding-left: 18px; font-size: 9.5px; }

  .contacts { list-style: none; position: absolute; left: 42px; top: 168px; }
  .contacts li {
    display: flex; align-items: center; gap: 12px;
    font-size: 15px; font-weight: 400; color: var(--ink); margin-bottom: 5px;
  }
  .contacts svg { width: 13px; height: 13px; flex: none; fill: none; stroke: var(--ink-soft); stroke-width: 1.6; }

  .details { position: absolute; right: 36px; top: 38px; text-align: right; }
  .motto {
    font-family: "Cormorant Garamond", serif; font-weight: 500;
    font-size: 15px; letter-spacing: .04em; color: var(--ink-soft); margin-bottom: 18px;
  }
  .person { font-size: 13.5px; line-height: 1.45; color: var(--ink); }
  .person .name {
    font-family: "Cormorant Garamond", serif; font-weight: 500;
    font-size: 21px; letter-spacing: .03em;
  }
  .person .creds { font-size: 13.5px; }
  .address { margin-top: 16px; font-size: 13.5px; line-height: 1.45; color: var(--ink); }

  .side-tab { position: absolute; right: 0; top: 56px; width: 14px; height: 12px; background: var(--slate); }

  .footer-band { position: absolute; left: 0; bottom: 0; width: 600px; height: 70px; }
  .footer-text {
    position: absolute; left: 26px; bottom: 14px;
    font-family: "Cormorant Garamond", serif; font-weight: 500;
    font-size: 17px; letter-spacing: .05em; color: var(--on-slate);
  }
</style>
</head>
<body>

  <section class="card card--front" aria-label="Business card front">
    <div class="brand">
      <div class="wordmark">TALLOWMERE WEALTH</div>
      <div class="tagline">STRATEGIC FINANCIAL ADVICE</div>
    </div>
    <div class="front-circle" aria-hidden="true"></div>

    <ul class="services">
      <li><svg viewBox="0 0 16 16"><circle cx="8" cy="8" r="6.6" fill="none" stroke="#f2f4f5" stroke-width="1.3"/><path d="M5.3 11V8.5M8 11V5.5M10.7 11V7" stroke="#f2f4f5" stroke-width="1.3"/></svg>Life &amp; TPD Insurance</li>
      <li><svg viewBox="0 0 16 16"><circle cx="8" cy="8" r="6.6" fill="none" stroke="#f2f4f5" stroke-width="1.3"/><path d="M5.3 11V8.5M8 11V5.5M10.7 11V7" stroke="#f2f4f5" stroke-width="1.3"/></svg>Income Protection</li>
      <li><svg viewBox="0 0 16 16"><circle cx="8" cy="8" r="6.6" fill="none" stroke="#f2f4f5" stroke-width="1.3"/><path d="M5.3 11V8.5M8 11V5.5M10.7 11V7" stroke="#f2f4f5" stroke-width="1.3"/></svg>Financial Planning</li>
      <li><svg viewBox="0 0 16 16"><circle cx="8" cy="8" r="6.6" fill="none" stroke="#f2f4f5" stroke-width="1.3"/><path d="M5.3 11V8.5M8 11V5.5M10.7 11V7" stroke="#f2f4f5" stroke-width="1.3"/></svg>Retirement Planning</li>
    </ul>

    <p class="licensee">Meridian Advisory Services Limited<br>Australian Financial Services Licensee-License Number 418207</p>
  </section>

  <section class="card card--back" aria-label="Business card back">
    <div class="brand">
      <div class="back-circle" aria-hidden="true"></div>
      <div class="wordmark">TALLOWMERE WEALTH</div>
      <div class="tagline">STRATEGIC FINANCIAL ADVICE</div>
    </div>

    <ul class="contacts">
      <li><svg viewBox="0 0 14 14"><rect x="3.5" y="1" width="7" height="12" rx="1.2"/><path d="M6 11h2"/></svg>0412 555 018</li>
      <li><svg viewBox="0 0 14 14"><path d="M2 5c0-2 2-3 5-3s5 1 5 3l-2 1-1-2H5L4 6 2 5z"/><rect x="3" y="7" width="8" height="5" rx="1"/></svg>(07) 5550 1234</li>
      <li><svg viewBox="0 0 14 14"><rect x="2" y="5" width="10" height="7" rx="1"/><path d="M4 5V2h6v3M4.5 8.5h5"/></svg>(07) 5550 5678</li>
      <li><svg viewBox="0 0 14 14"><rect x="1.5" y="3" width="11" height="8" rx="1"/><path d="M1.5 3.5 7 8l5.5-4.5"/></svg>sam@tallowmerewealth.com.au</li>
      <li><svg viewBox="0 0 14 14"><circle cx="7" cy="7" r="5.5"/><path d="M1.5 7h11M7 1.5c-2.4 3-2.4 8 0 11M7 1.5c2.4 3 2.4 8 0 11"/></svg>www.tallowmerewealth.com.au</li>
    </ul>

    <div class="details">
      <p class="motto">'FINANCIAL PEACE OF MIND'</p>
      <div class="person">
        <p><span class="name">SAM CARTER</span> <span class="creds">| B.Ag.Ec. Dip F.P. CFP®</span></p>
        <p>Managing Director</p>
        <p>Authorised Representative</p>
      </div>
      <div class="address">
        <p>Suite 4A, 18 Harlow St</p>
        <p>Riverside QLD 4170</p>
        <p>PO Box 3152</p>
        <p>Eastwood QLD 4171</p>
      </div>
    </div>

    <div class="side-tab" aria-hidden="true"></div>

    <svg class="footer-band" viewBox="0 0 600 70" aria-hidden="true">
      <polygon points="0,28 380,28 392,18 430,18 600,70 0,70" fill="none"/>
      <polygon points="0,30 400,30 425,16 600,16 600,18 430,18 440,70 0,70" fill="#5f6a70"/>
    </svg>
    <p class="footer-text">A REFERRAL BUILT BUSINESS</p>
  </section>

</body>
</html>
```